Modern design company business card design

We are a design oriented construction firm. The owner is an architect and licensed General Contractor and accomplished furniture designer. We do new home construction and large scale remodeling and office design. We would like a design for our new business cards that is clean and modern, but relatable. We like the bright green color of our logo mixed with different shades of grey. We're also open to reinterpreting the logo.

Target Market(s)

Potential design clients,
Construction clients

Industry/Entity Type

Architecture

Contact Information for Business Card

Tall Maple Design | Build Inc. (optional with logo, Inc. optional)Jeffrey MorganOwner (optional)317.555.0148 cell317.431.8056 officejmorgan@greensquareinc.comwww.greensquareinc.com

Font styles to use
Sans Serif
Other font styles liked:
• Avenir

Requirements
Nice to have
• I like designs that have some continuity between the front and back, i.e. similar layouts or graphic elements that wrap around the card. I tend to prefer horizontal over vertical, but that's not a have to. I also tend to prefer white or recycled paper.

```html
<!DOCTYPE html>
<html lang="en">
<head>
<meta charset="utf-8">
<title>Tall Maple Design | Build — Business Card</title>
<link rel="stylesheet" href="https://fonts.googleapis.com/css2?family=Mulish:ital,wght@0,400;0,700;1,400&display=swap">
<style>
  :root {
    --stage: #3b3b3c;
    --paper: #ffffff;
    --card-grey: #939598;
    --text-grey: #8a8b8e;
    --ink: #4a4b4d;
    --green: #7cc24e;
    --green-light: #c6dd6a;
    --band-grey: #939598;
    --white: #ffffff;
  }
  * { box-sizing: border-box; margin: 0; padding: 0; }
  html, body {
    width: 1105px; height: 1200px; overflow: hidden;
    background: var(--stage);
    font-family: "Mulish", sans-serif;
  }
  .canvas { position: relative; width: 1105px; height: 1200px; }
  .card {
    position: absolute; left: 196px; width: 720px; height: 412px; overflow: hidden;
  }
  .card--front { top: 146px; background: var(--paper); }
  .card--back { top: 602px; background: var(--card-grey); }

  .brand { position: absolute; left: 38px; top: 96px; }
  .brand__name {
    white-space: nowrap;
    font-size: 38px; font-weight: 400; letter-spacing: 1px; line-height: 1;
    color: var(--text-grey);
  }
  .brand__tagline {
    margin-top: 12px; white-space: nowrap;
    font-size: 14px; font-weight: 400; letter-spacing: 1.5px; color: var(--text-grey);
  }

  .contact { position: absolute; left: 38px; top: 233px; list-style: none; }
  .contact__item {
    display: flex; align-items: center; height: 27.5px;
    font-size: 20px; color: var(--ink);
  }
  .contact__icon { width: 18px; height: 18px; margin-right: 9px; fill: var(--green); }

  .person { position: absolute; right: 48px; top: 262px; text-align: right; }
  .person__name { font-size: 27px; font-weight: 700; color: var(--green); line-height: 1.2; }
  .person__role { font-size: 20px; color: var(--text-grey); line-height: 1.2; }

  .band { position: absolute; left: 0; bottom: 0; width: 100%; height: 28px; display: flex; }
  .band__green { width: 561px; height: 100%; background: linear-gradient(180deg, var(--green-light), var(--green)); }
  .band__grey { flex: 1; height: 100%; background: var(--band-grey); }

  .back__name {
    position: absolute; right: 42px; top: 296px; white-space: nowrap;
    font-size: 34px; font-weight: 400; letter-spacing: 1px; line-height: 1;
    color: var(--white);
  }
  .back__url {
    position: absolute; right: 42px; top: 354px;
    font-size: 19px; font-style: italic; color: var(--white);
  }
</style>
</head>
<body>
<main class="canvas">
  <section class="card card--front" aria-label="Business card front">
    <div class="brand">
      <div class="brand__name">Tall Maple</div>
      <div class="brand__tagline">DESIGN | BUILD</div>
    </div>

    <ul class="contact">
      <li class="contact__item">
        <svg class="contact__icon" viewBox="0 0 24 24" aria-hidden="true"><path d="M6.6 10.8a15.2 15.2 0 0 0 6.6 6.6l2.2-2.2c.3-.3.7-.4 1-.2 1.1.4 2.3.6 3.6.6.6 0 1 .4 1 1V20c0 .6-.4 1-1 1A17 17 0 0 1 3 4c0-.6.4-1 1-1h3.5c.6 0 1 .4 1 1 0 1.3.2 2.5.6 3.6.1.3 0 .7-.2 1z"/></svg>
        317.555.0148
      </li>
      <li class="contact__item">
        <svg class="contact__icon" viewBox="0 0 24 24" aria-hidden="true"><path d="M8 1h8a2 2 0 0 1 2 2v18a2 2 0 0 1-2 2H8a2 2 0 0 1-2-2V3a2 2 0 0 1 2-2zm0 3v14h8V4zm4 15.5a1.2 1.2 0 1 0 0 2.4 1.2 1.2 0 0 0 0-2.4z"/></svg>
        317.555.0172
      </li>
      <li class="contact__item">
        <svg class="contact__icon" viewBox="0 0 24 24" aria-hidden="true"><path d="M12 2a10 10 0 1 0 0 20 10 10 0 0 0 0-20zm-1 17.9A8 8 0 0 1 4.2 10L9 14.8v1a2 2 0 0 0 2 2zm6.9-2.5A2 2 0 0 0 16 16h-1v-3a1 1 0 0 0-1-1H8v-2h2a1 1 0 0 0 1-1V7h2a2 2 0 0 0 2-2v-.4a8 8 0 0 1 2.9 12.8z"/></svg>
        www.tallmapleinc.example
      </li>
      <li class="contact__item">
        <svg class="contact__icon" viewBox="0 0 24 24" aria-hidden="true"><path d="M2 5h20v14H2zm2 2v.5l8 5 8-5V7zm0 2.8V17h16V9.8l-8 5z"/></svg>
        dholloway@tallmapleinc.example
      </li>
    </ul>

    <div class="person">
      <div class="person__name">Dennis Holloway</div>
      <div class="person__role">Owner</div>
    </div>

    <div class="band">
      <div class="band__green"></div>
      <div class="band__grey"></div>
    </div>
  </section>

  <section class="card card--back" aria-label="Business card back">
    <div class="back__name">Tall Maple</div>
    <div class="back__url">www.tallmapleinc.example</div>
  </section>
</main>
</body>
</html>
```